Yacht, Boats, Watersports company needs a redesign of business card

Hello Designers!
We are a Boat dealership company that sells fun in the water, we sell boats, Yachts, Kayaks and also yacht WaterSport toys. We are looking to redesign our business cards in to something a little bit more sophisticated. in a way that we can make better use of our company colors. I'm attaching a zipped file containing the company 3 sets of company logo which one is an horizontal another one is a vertical and also a chromed 3d logo. Also is included two set of business cards that we use and also some designs that i think it's interesting. We use PMS 2026c Orange and PMS 7687C Blue. I would like to see at least two different options with the orange as accent and also using blue as an accent color. It's really important for the business cards to have a font option and size that is legible to most people. Our current website is wwww.coralpennant.com. Please visit if you want to have a better feeling of the Boat dealership
You can send Single sided or double side options. We are now using single sided but we may be open for a double side option if we really like the design.
Target Market(s)
Marine, boat sales, yacht sales, water toys sales/
Contact Information for Business Card
Name: Dale Whitcombe
Address: 212 North Fenwick Lane,
Port Alder, GA 31999
Phone: 555-731-8842
Fax: 954:731-8843
Cell: 555-382-1490
Email: dw@coralpennant.com
Website: coralpennant.com
Requirements
Must have
- the current information of the business card provided.
logo
use the PMS Colors
Nice to have
- a touch of elegance and sophistication but simple
Should not have
- should not have any typography that is hard to read, the card should be simple but yet sophisticated.

```html
<!DOCTYPE html>
<html lang="en">
<head>
<meta charset="utf-8">
<title>Coral Pennant Marine Center – Business Card</title>
<link rel="stylesheet" href="https://fonts.googleapis.com/css2?family=Montserrat:wght@600;800&family=Poppins:wght@400&display=swap">
<style>
  :root {
    --blue: #1a5dab;
    --blue-deep: #1462b4;
    --blue-light: #4fb6f0;
    --orange: #f07a18;
    --ink: #3a3a3a;
    --paper: #ffffff;
    --bg: #c4c4c4;
  }
  * { box-sizing: border-box; margin: 0; padding: 0; }
  html, body { width: 1200px; height: 800px; overflow: hidden; }
  body {
    background: var(--bg);
    display: flex;
    flex-direction: column;
    align-items: center;
    justify-content: center;
    gap: 40px;
    font-family: "Poppins", sans-serif;
  }
  .card {
    position: relative;
    width: 588px;
    height: 336px;
    border-radius: 24px;
    border-bottom: 3px solid var(--orange);
    overflow: hidden;
  }
  .card--front { background: var(--paper); }
  .card--back {
    background: var(--blue-deep);
    display: flex;
    align-items: center;
    justify-content: center;
  }

  .brand {
    position: absolute;
    top: 38px;
    right: 44px;
    display: flex;
    align-items: center;
    gap: 12px;
  }
  .brand__mark {
    width: 34px;
    height: 34px;
    border-radius: 50%;
    background: var(--orange);
  }
  .brand__name {
    font-family: "Montserrat", sans-serif;
    font-weight: 800;
    font-size: 22px;
    line-height: 1.1;
    letter-spacing: 0.5px;
    text-transform: uppercase;
    color: var(--blue);
  }

  .holder {
    position: absolute;
    left: 40px;
    top: 170px;
    font-family: "Montserrat", sans-serif;
    font-weight: 800;
    font-size: 22px;
    text-transform: uppercase;
    color: var(--blue);
  }
  .divider {
    position: absolute;
    left: 40px;
    right: 40px;
    top: 203px;
    height: 1px;
    background: var(--blue);
  }

  .contacts {
    position: absolute;
    left: 44px;
    top: 214px;
    list-style: none;
    font-size: 15px;
    line-height: 22px;
    color: var(--ink);
  }
  .contacts li { display: flex; align-items: center; gap: 10px; }
  .contacts svg { width: 12px; height: 12px; fill: var(--blue); flex: none; }

  .address {
    position: absolute;
    right: 40px;
    top: 214px;
    text-align: right;
    font-style: normal;
    font-size: 14px;
    line-height: 22px;
    color: var(--ink);
  }

  .brand--reverse {
    position: static;
    flex-direction: column;
    gap: 14px;
  }
  .brand--reverse .brand__mark {
    width: 70px;
    height: 70px;
    background: none;
    border: 5px solid var(--blue-light);
  }
  .brand--reverse .brand__name {
    font-size: 34px;
    color: var(--blue-light);
    text-align: center;
  }
</style>
</head>
<body>
  <section class="card card--front" aria-label="Business card front">
    <div class="brand">
      <span class="brand__mark"></span>
      <span class="brand__name">Coral Pennant<br>Marine Center</span>
    </div>

    <h1 class="holder">Dale Whitcombe</h1>
    <div class="divider"></div>

    <ul class="contacts">
      <li>
        <svg viewBox="0 0 12 12" aria-hidden="true"><path d="M2.5 0.5l2 2-1 1.5c.8 1.6 2 2.8 3.5 3.5l1.5-1 2 2-1.5 2C4.5 10.5 1.5 7.5 0.5 2z"/></svg>
        555-731-8842
      </li>
      <li>
        <svg viewBox="0 0 12 12" aria-hidden="true"><path d="M3 0h6v12H3zM4 1.5v8h4v-8z"/></svg>
        555-382-1490
      </li>
      <li>
        <svg viewBox="0 0 12 12" aria-hidden="true"><path d="M3 0h5v3H3zM1 4h10v6H9v2H3v-2H1zM4 8v3h4V8z"/></svg>
        555-731-8843
      </li>
      <li>
        <svg viewBox="0 0 12 12" aria-hidden="true"><path d="M0 2h12v8H0zM1 3l5 4 5-4v-.2H1z"/></svg>
        dw@coralpennant.com
      </li>
    </ul>

    <address class="address">
      Coral Pennant Marine Center<br>
      212 North Fenwick Lane<br>
      Port Alder, GA 31999<br>
      www.coralpennant.com
    </address>
  </section>

  <section class="card card--back" aria-label="Business card back">
    <div class="brand brand--reverse">
      <span class="brand__mark"></span>
      <span class="brand__name">Coral Pennant<br>Marine Center</span>
    </div>
  </section>
</body>
</html>
```